Website for IT consulting Company

I need a website upgrade, the existing site content is ok, I would also like to add a testimonial page, the site should be something that is easy for us to update content. You use the content from www.kelvanbrook.com as an example. I will also post update logo and artwork. I also need a contact form with some type of validation or captcha.

I added Coded to the Project

Please omit Address maps

Target Market(s)

small business, service oriented companies. We provide IT Consulting, support and mangement

Industry/Entity Type

Information Technology

Coding

Number of Pages Required

1 page

Font styles to use
Serif
Sans Serif

Requirements
Must have
• Contain logo attached, and content from existing web site www.kelvanbrook.com.
• Also need to update content easily, and be movable to different platforms.
• There is a catch phrase
• "Let us worry about your technology…” “ so you don’t have to!”
• Should be included.
Nice to have
• Testimonial page, Project page where we can post new and past projects and pictures
Should not have
• none

```html
<!DOCTYPE html>
<html lang="en">
<head>
<meta charset="utf-8">
<title>Kelvanbrook Consulting Group — IT Solutions</title>
<link rel="stylesheet" href="https://fonts.googleapis.com/css2?family=Roboto:wght@400;500;700&family=Roboto+Condensed:wght@300;400&display=swap">
<style>
  :root {
    --hero-deep: #2a7fc0;
    --hero-mid: #4aa0d6;
    --hero-light: #6fb8e2;
    --band-blue: #2f95dc;
    --accent-blue: #1e88d8;
    --white: #ffffff;
    --ink: #1f2a33;
    --rule: rgba(255,255,255,0.75);
    --chart-line: rgba(255,255,255,0.5);
    --chart-dot: rgba(255,255,255,0.7);
  }
  * { box-sizing: border-box; margin: 0; padding: 0; }
  html, body { width: 1200px; height: 676px; overflow: hidden; background: var(--white); }
  body { font-family: "Roboto", Arial, sans-serif; color: var(--white); }

  .site { position: relative; width: 1200px; height: 676px; overflow: hidden; }

  .hero {
    position: absolute; left: 0; top: 0; width: 1200px; height: 492px;
    background:
      radial-gradient(ellipse at 25% 45%, rgba(150,205,240,0.35), transparent 60%),
      radial-gradient(ellipse at 80% 30%, rgba(120,190,235,0.35), transparent 55%),
      linear-gradient(160deg, var(--hero-deep) 0%, var(--hero-mid) 45%, var(--hero-light) 100%);
  }

  .topbar {
    position: absolute; left: 0; top: 0; width: 100%; height: 72px;
    border-bottom: 1px solid rgba(255,255,255,0.35);
    display: flex; align-items: center; padding: 0 34px;
  }
  .brand { display: flex; align-items: center; gap: 10px; width: 300px; }
  .brand-mark { width: 22px; height: 22px; background: var(--white); }
  .brand-text { display: flex; flex-direction: column; }
  .brand-name { font-size: 24px; font-weight: 700; letter-spacing: 0.5px; line-height: 1; }
  .brand-tagline { font-size: 6.5px; font-weight: 400; margin-top: 3px; opacity: 0.9; }

  .main-nav { display: flex; gap: 36px; margin-left: 40px; font-size: 14px; font-weight: 400; }
  .main-nav a { color: var(--white); text-decoration: none; }

  .nav-actions { margin-left: auto; display: flex; gap: 6px; }
  .btn-login, .btn-contact {
    font-size: 11px; font-weight: 500; padding: 7px 12px; border-radius: 16px;
  }
  .btn-login { border: 1.5px solid var(--white); color: var(--white); }
  .btn-contact { background: var(--white); color: var(--ink); border: 1.5px solid var(--white); }

  .hero-copy { position: absolute; left: 0; top: 215px; width: 100%; text-align: center; }
  .hero-title { font-size: 26px; font-weight: 700; }
  .hero-sub { font-family: "Roboto Condensed", "Arial Narrow", sans-serif; font-weight: 300; font-size: 25px; margin-top: 14px; }
  .btn-learn {
    display: inline-block; margin-top: 20px; font-size: 11px; font-weight: 700;
    border: 1.5px solid var(--white); border-radius: 3px; padding: 8px 16px;
  }

  .trend-chart { position: absolute; left: 0; top: 380px; width: 1200px; height: 110px; }

  .welcome-band {
    position: absolute; left: 0; top: 492px; width: 1200px; height: 124px;
    background: var(--band-blue); text-align: center; padding-top: 10px;
  }
  .welcome-title { font-size: 19px; font-weight: 700; }
  .welcome-rule { width: 1040px; margin: 10px auto 14px; border-top: 1px dashed var(--rule); }
  .welcome-text { font-size: 11.5px; line-height: 1.55; width: 1000px; margin: 0 auto; }

  .solutions { position: absolute; left: 0; top: 616px; width: 1200px; height: 60px; background: var(--white); text-align: center; padding-top: 12px; }
  .solutions-title { font-size: 19px; font-weight: 500; color: var(--ink); }
  .solutions-title span { color: var(--accent-blue); }
  .solutions-rule { width: 1060px; margin: 12px auto 0; border-top: 1px dashed var(--accent-blue); }
</style>
</head>
<body>
<div class="site">
  <section class="hero" role="img" aria-label="Blurred photo of a team working at laptops and documents on a desk, tinted blue">
    <header class="topbar">
      <div class="brand">
        <span class="brand-mark"></span>
        <div class="brand-text">
          <span class="brand-name">Kelvanbrook</span>
          <span class="brand-tagline">Let us worry about your technology… So you don't have to!</span>
        </div>
      </div>
      <nav class="main-nav">
        <a href="#">ABOUT</a><a href="#">SUPPORT</a><a href="#">CLIENTS</a><a href="#">PROJECT</a><a href="#">CAREERS</a>
      </nav>
      <div class="nav-actions">
        <span class="btn-login">Log In</span>
        <span class="btn-contact">Contact Us</span>
      </div>
    </header>

    <div class="hero-copy">
      <h1 class="hero-title">IT solutions that work for your business.</h1>
      <p class="hero-sub">A full service technology company.</p>
      <span class="btn-learn">Learn More</span>
    </div>

    <svg class="trend-chart" viewBox="0 0 1200 110" aria-hidden="true">
      <polyline fill="none" stroke="var(--chart-line)" stroke-width="1.5"
        points="20,80 60,72 100,76 140,64 180,68 220,58 260,62 300,50 340,56 380,46 420,52 460,60 500,54 540,44 580,48 620,38 660,42 700,50 740,46 780,36 820,40 860,30 900,36 940,44 980,38 1020,28 1060,34 1100,24 1140,30 1180,22"/>
      <g fill="none" stroke="var(--chart-dot)" stroke-width="1.5">
        <circle cx="60" cy="72" r="4"/><circle cx="100" cy="76" r="4"/><circle cx="140" cy="64" r="4"/><circle cx="180" cy="68" r="4"/>
        <circle cx="220" cy="58" r="4"/><circle cx="260" cy="62" r="4"/><circle cx="300" cy="50" r="4"/><circle cx="340" cy="56" r="4"/>
        <circle cx="380" cy="46" r="4"/><circle cx="420" cy="52" r="4"/><circle cx="460" cy="60" r="4"/><circle cx="500" cy="54" r="4"/>
        <circle cx="540" cy="44" r="4"/><circle cx="580" cy="48" r="4"/><circle cx="620" cy="38" r="4"/><circle cx="660" cy="42" r="4"/>
        <circle cx="700" cy="50" r="4"/><circle cx="740" cy="46" r="4"/><circle cx="780" cy="36" r="4"/><circle cx="820" cy="40" r="4"/>
        <circle cx="860" cy="30" r="4"/><circle cx="900" cy="36" r="4"/><circle cx="940" cy="44" r="4"/><circle cx="980" cy="38" r="4"/>
        <circle cx="1020" cy="28" r="4"/><circle cx="1060" cy="34" r="4"/><circle cx="1100" cy="24" r="4"/><circle cx="1140" cy="30" r="4"/>
      </g>
    </svg>
  </section>

  <section class="welcome-band">
    <h2 class="welcome-title">Welcome to Kelvanbrook Consulting Group, Inc</h2>
    <div class="welcome-rule"></div>
    <p class="welcome-text">Outsourcing is subcontracting a process, such as product design or manufacturing, to a third-party company.[1] The decision to outsource is often made in the interest of lowering firm costs, redirecting or conserving energy directed at the competencies of a particular business, or to make more efficient use of land, labor, capital, (information) technology and resources. Outsourcing became part of the business lexicon during the 1980s</p>
  </section>

  <section class="solutions">
    <h2 class="solutions-title">IT Support <span>Solutions</span></h2>
    <div class="solutions-rule"></div>
  </section>
</div>
</body>
</html>
```